Rebrand stationary with recently completed logo design

Need new business cards, thank you cards, letterhead, envelopes and presentation folders. The designs will be sent to a separate production firm so I need the files to be print ready.

My contact info
Reko Haliburn

Office 604-318-5047
Fax 604-371-8054

Email reko@glazemark.ca
website www.glazemark.ca

315-14720 62nd Avenue,
Langley, BC, V2K 3R8

Target Market(s)

Homeowners, businesses and contractors

Industry/Entity Type

Business

Font styles to use
Sans Serif

Colors
34a7d7

Requirements
Must have
• Like to have one side of the business card a solid color with the logo in all white. The side with all the text to be a white background
• I find the current blue on the front of the card with the white logo too dark.
Should not have
• Gradient colors

```html
<!DOCTYPE html>
<html lang="en">
<head>
<meta charset="utf-8">
<title>Glazemark Business Card</title>
<link rel="stylesheet" href="https://fonts.googleapis.com/css2?family=Open+Sans:wght@300;400;600&display=swap">
<style>
  :root {
    --backdrop: #e9e7e3;
    --slate: #47535d;
    --paper: #f6f6f6;
    --white: #ffffff;
    --brand-blue: #1a9ad6;
    --ink: #4b4f53;
    --muted: #8d969c;
    --back-muted: #8e9aa3;
    --rule: #b9bec2;
    --curl-shadow: #d9dcde;
  }
  * { margin: 0; padding: 0; box-sizing: border-box; }
  html, body {
    width: 1200px; height: 960px; overflow: hidden;
    background: var(--backdrop);
    font-family: "Open Sans", Arial, sans-serif;
  }
  .canvas { position: relative; width: 1200px; height: 960px; }

  .card { position: absolute; }
  .card-front {
    left: 302px; top: 130px; width: 600px; height: 340px;
    background: var(--slate);
  }
  .card-front .face {
    position: absolute; left: 14px; top: 13px; width: 572px; height: 314px;
    background: var(--paper);
  }
  .card-back {
    left: 298px; top: 488px; width: 600px; height: 342px;
    background: var(--white);
  }
  .card-back .face {
    position: absolute; left: 14px; top: 13px; width: 572px; height: 316px;
    background: var(--slate);
  }
  .curl { position: absolute; right: 14px; bottom: 13px; width: 52px; height: 56px; }

  .wordmark { position: absolute; display: flex; align-items: center; gap: 12px; }
  .wordmark-square { flex: none; }
  .wordmark-name { font-weight: 400; letter-spacing: 0.5px; line-height: 1; }
  .tagline { position: absolute; font-weight: 400; letter-spacing: 1.3px; line-height: 1; }

  .front-mark { left: 70px; top: 184px; }
  .front-mark .wordmark-square { width: 16px; height: 16px; background: var(--slate); }
  .front-mark .wordmark-name { font-size: 33px; color: var(--brand-blue); }
  .front-tagline { left: 70px; top: 221px; font-size: 14px; color: var(--muted); }

  .divider {
    position: absolute; left: 316px; top: 80px; width: 1px; height: 160px;
    background: var(--rule);
  }
  .contact { position: absolute; left: 345px; top: 82px; color: var(--ink); }
  .contact-name {
    font-size: 18px; font-weight: 600; color: var(--brand-blue);
    letter-spacing: 0.2px; margin-bottom: 10px;
  }
  .contact-address { font-size: 13px; line-height: 18px; margin-bottom: 12px; }
  .contact-list { list-style: none; font-size: 13px; }
  .contact-list li { display: flex; align-items: center; height: 19.5px; }
  .contact-list svg { width: 13px; height: 13px; margin-right: 10px; fill: var(--brand-blue); }

  .back-mark { left: 112px; top: 122px; }
  .back-mark .wordmark-square { width: 22px; height: 22px; background: var(--white); }
  .back-mark .wordmark-name { font-size: 44px; color: var(--white); }
  .back-tagline { left: 192px; top: 170px; font-size: 16px; color: var(--back-muted); }
</style>
</head>
<body>
<main class="canvas">

  <section class="card card-front" aria-label="Business card, contact side">
    <div class="face">
      <div class="wordmark front-mark">
        <span class="wordmark-square"></span>
        <span class="wordmark-name">GLAZEMARK</span>
      </div>
      <div class="tagline front-tagline">LIGHT, SHADE &amp; PRIVACY</div>

      <div class="divider"></div>

      <div class="contact">
        <div class="contact-name">REKO HALIBURN</div>
        <div class="contact-address">315-14720 62nd Avenue<br>Langley, BC, V2K 3R8</div>
        <ul class="contact-list">
          <li><svg viewBox="0 0 16 16"><path d="M3.5 1l3 3-1.8 2a9 9 0 0 0 5.3 5.3l2-1.8 3 3-2 2C6.5 14.5 1.5 9.5 1.5 3z"/></svg>604-318-5047</li>
          <li><svg viewBox="0 0 16 16"><path d="M4 1h8v4H4zM1 6h14v6h-3v3H4v-3H1zM5 10v3h6v-3z"/></svg>604-371-8054</li>
          <li><svg viewBox="0 0 16 16"><path d="M1 3h14v10H1zM2.5 4.5L8 9l5.5-4.5v-.5h-11z" fill-rule="evenodd"/></svg>reko@glazemark.ca</li>
          <li><svg viewBox="0 0 16 16"><circle cx="8" cy="8" r="7"/><path d="M4 5h3v3H5zM9 9h3l-1 3H9z" fill="#f6f6f6"/></svg>www.glazemark.ca</li>
        </ul>
      </div>
    </div>
    <svg class="curl" viewBox="0 0 52 56" aria-hidden="true">
      <path d="M52 0 V56 H0 C18 55 30 50 36 38 C40 28 40 16 44 10 C46 6 49 3 52 0 Z" fill="var(--slate)"/>
      <path d="M0 56 C18 55 30 50 36 38 C38 46 30 54 16 56 Z" fill="var(--curl-shadow)"/>
      <path d="M44 10 C47 6 50 4 52 4 V8 C49 8 46 9 44 10 Z" fill="var(--paper)"/>
    </svg>
  </section>

  <section class="card card-back" aria-label="Business card, logo side">
    <div class="face">
      <div class="wordmark back-mark">
        <span class="wordmark-square"></span>
        <span class="wordmark-name">GLAZEMARK</span>
      </div>
      <div class="tagline back-tagline">LIGHT, SHADE &amp; PRIVACY</div>
    </div>
    <svg class="curl" viewBox="0 0 52 56" aria-hidden="true">
      <path d="M52 0 V56 H0 C18 55 30 50 36 38 C40 28 40 16 44 10 C46 6 49 3 52 0 Z" fill="var(--white)"/>
      <path d="M0 56 C18 55 30 50 36 38 C38 46 30 54 16 56 Z" fill="var(--curl-shadow)"/>
      <path d="M44 10 C47 6 50 4 52 4 V8 C49 8 46 9 44 10 Z" fill="var(--slate)"/>
    </svg>
  </section>

</main>
</body>
</html>
```